South Florida Real Estate Brokerage Business

The name is LAKE VORISSA REAL ESTATE.
The company is a Real estate realty based in Miami.
Is targeted to Latin American clients.
Must express luxury, and efficiency.
Target clients for properties around 250k to a million +.
Vorissa means Royal in Latin.
Should communicate safety and knowledge of the product and transaction with a tech edge.

The web design needs to be a Social tool, with Friendloop and other media integration of some sort. Needs to have a Show case place, a Search place (MLS listings) with maps and filters.
Needs to reflect luxury but also mixed with a social edge capable of engaging clients or transition them to communicate with the page.
Include the logo from the uploaded files, feel free to change the color or font per webdesign.
This is a Front en design, layout and graphics.
Possible future programming if approved.
I can receive Quotes for the Code part.

Spanish and English speakers living in Latin America and Canada looking for apartments and houses to buy.

Business

• Search area.
Neighbourhood area.
Could be a blog or news area.
Client registration.
Social Plugin
• Social linking to networks.
Log in with friendloop account.
Friendloop Like.

```html
<!DOCTYPE html>
<html lang="en">
<head>
<meta charset="utf-8">
<title>Lake Vorissa Real Estate</title>
<link href="https://fonts.googleapis.com/css2?family=Libre+Baskerville&family=PT+Sans:ital,wght@0,400;0,700;1,400&family=Oswald:wght@500&display=swap" rel="stylesheet">
<style>
:root{
  --ink:#1c1c1c;
  --gold:#c8a063;
  --gold-dark:#a97d3c;
  --gold-band:#c4924a;
  --gold-text:#c9a466;
  --brown:#8a6428;
  --cream:#ece4d4;
  --panel:#f7f3ec;
  --paper:#f0f0f0;
  --white:#ffffff;
  --text:#222222;
}
*{box-sizing:border-box;margin:0;padding:0}
html,body{width:1000px;height:1200px;overflow:hidden}
body{position:relative;background:var(--paper);font-family:"PT Sans",Arial,sans-serif;color:var(--text)}
.abs{position:absolute}
.top-band{left:0;top:0;width:1000px;height:480px;background:var(--ink)}
.brand{left:120px;top:10px;width:205px;text-align:center}
.brand-mark{display:block;width:40px;height:40px;margin:12px auto 14px;background:var(--gold)}
.brand-name{font-size:22px;color:var(--gold-text);letter-spacing:1px;line-height:1;border-bottom:1px solid var(--gold-text);padding-bottom:5px}
.brand-sub{font-size:15px;color:var(--gold-text);letter-spacing:1px;margin-top:4px}
.login{left:573px;top:18px;width:320px}
.login-title{font-size:12px;color:var(--gold-text);text-transform:uppercase;margin-bottom:5px}
.login-row{display:flex;gap:5px}
.login-input{width:131px;height:20px;background:var(--white);font-size:10px;color:#555;padding:3px 5px}
.login-btn{width:43px;height:19px;background:linear-gradient(#e2c283,var(--gold-dark));border-radius:3px;font-size:11px;color:#3a2a10;text-align:center;line-height:19px;margin-left:1px}
.login-help{font-size:10px;color:#aaa;margin-top:3px}
.nav{left:362px;top:94px;width:537px;height:37px;background:linear-gradient(#d8b272,var(--gold-dark));border-radius:4px 4px 0 0;display:flex}
.nav a{flex:auto;text-align:center;white-space:nowrap;color:var(--white);text-decoration:none;font-size:13px;line-height:37px;padding:0 6px;border-right:1px solid rgba(90,60,20,.35);border-left:1px solid rgba(255,235,190,.3)}
.nav a:last-child{border-right:none}
.hero{left:101px;top:133px;width:798px;height:354px;background:var(--gold)}
.hero-photo{left:109px;top:141px;width:782px;height:339px;background:linear-gradient(#9cc0e0 0%,#c6d9e8 25%,#9a8a70 45%,#6e6552 65%,#4f7a2c 80%,#3e6a22 100%)}
.hero-arrow{top:286px;width:52px;height:52px;border-radius:50%;background:var(--gold);opacity:.9}
.welcome-band{left:101px;top:487px;width:798px;height:200px;background:var(--cream)}
.welcome{left:126px;top:500px;width:345px}
.welcome h1{font-weight:400;font-size:26px;color:#333;line-height:1.1}
.welcome h2{font-family:"Libre Baskerville",serif;font-weight:400;font-size:22px;color:var(--brown);margin:2px 0 10px;line-height:1.2}
.welcome p{font-size:10.5px;line-height:16px;color:#222}
.search-tab{left:510px;top:424px;width:171px;height:32px;background:var(--gold);border:2px solid #e6cc96;border-bottom:none;font-size:16px;color:#2a2a2a;text-align:center;line-height:32px}
.search{left:501px;top:455px;width:382px;height:218px;background:var(--panel);border:2px solid var(--white);box-shadow:0 1px 3px rgba(0,0,0,.15)}
.quick{position:absolute;left:0;top:0;width:378px;height:52px;background:#e8dfcc}
.quick-label{position:absolute;left:16px;top:8px;font-size:14px;line-height:16px;text-align:center;color:#222}
.quick-field-label{position:absolute;left:84px;top:6px;font-size:12px;color:#222}
.field{position:absolute;background:var(--white);border:1px solid #ddd;font-size:10px;color:#777;padding:5px 7px}
.select::after{content:"";position:absolute;right:0;top:0;width:20px;height:100%;background:linear-gradient(#e0c48e,var(--gold-dark))}
.field-label{position:absolute;font-size:12px;color:#222}
.btn{position:absolute;height:25px;background:linear-gradient(#dcb97a,var(--gold-dark));border-radius:4px;color:var(--white);font-size:11px;font-weight:700;text-align:center;line-height:25px;white-space:nowrap}
.go{position:absolute;left:337px;top:19px;width:32px;height:26px;border-radius:4px;background:linear-gradient(#dcb97a,var(--gold-dark));color:var(--white);font-size:11px;font-weight:700;text-align:center;line-height:26px}
.adv{position:absolute;left:280px;top:176px;font-size:10px;color:var(--brown);font-weight:700}
.footer-band{left:0;top:993px;width:1000px;height:157px;background:var(--gold-band)}
.content{left:101px;top:687px;width:798px;height:323px;background:var(--white);box-shadow:0 2px 4px rgba(0,0,0,.2)}
.news{left:109px;top:695px;width:223px;height:307px;background:#ececec;padding:14px 16px}
.news-head{display:flex;justify-content:space-between;align-items:baseline;border-bottom:1px solid #ddd;padding-bottom:6px}
.news-head h3{font-weight:400;font-size:17px}
.news-head span{font-size:9px;color:#888}
.news-item{display:flex;gap:14px;padding:7px 0 9px;border-bottom:1px solid #ddd}
.news-item:last-child{border-bottom:none}
.date{flex:none;width:46px;height:46px;border-radius:50%;background:#e5dac6;text-align:center;font-size:10px;line-height:11px;padding-top:4px;color:#333}
.date b{display:block;font-size:14px;line-height:15px}
.news-item h4{font-size:10px;color:#4a3410;margin-bottom:3px}
.news-item p{font-size:10px;line-height:13px;color:#444}
.col-title{font-weight:400;font-size:17px;color:#222}
.feature-photo{left:363px;top:760px;width:167px;height:145px;background:linear-gradient(#4a6f9c 0%,#8aa4c4 35%,#e8e8e4 55%,#c8c8c0 75%,#4e7a30 100%);border:4px solid var(--white);box-shadow:0 1px 4px rgba(0,0,0,.3)}
.feature-back{left:369px;top:752px;width:172px;height:162px;background:#e7eadc;transform:rotate(-3deg)}
.slide-btn{width:24px;height:28px;border-radius:50%;background:#e2d6bf}
.divider{left:596px;top:725px;width:1px;height:275px;background:#ddd}
.map{left:616px;top:748px;width:148px;height:92px;background:linear-gradient(#f3e4b6,#e6cf92)}
.small-text{font-size:10px;line-height:15px;color:#222}
.testimonials{left:616px;top:870px;width:264px;height:130px;background:linear-gradient(#e9e9e9,#fafafa 60%);border-top:1px solid #ddd;padding:12px 12px}
.testimonials h3{font-weight:400;font-size:19px;color:#444;margin-bottom:5px}
.testimonials p{font-style:italic;font-size:10px;line-height:14px;color:#666;padding-left:2px}
.f-title{font-size:14px;color:#222}
.f-links{display:grid;grid-template-columns:110px 90px;gap:6px 0;margin-top:10px;padding-left:3px}
.f-links a{font-size:10px;color:var(--white);text-decoration:none}
.mail-title{display:inline-block;background:#111;color:var(--white);font-family:"Oswald",sans-serif;font-size:19px;padding:0 4px;line-height:24px;letter-spacing:.5px}
.mail-text{font-size:11px;color:var(--white);margin:10px 0 9px;line-height:14px}
.mail-field{position:relative;width:176px;height:22px;border-radius:11px;background:var(--white);font-size:10px;color:#555;padding:5px 9px}
.mail-join{position:absolute;right:0;top:0;width:32px;height:22px;border-radius:11px;background:#e07a24;color:var(--white);font-family:"Oswald",sans-serif;font-size:11px;text-align:center;line-height:22px}
.blog-date{font-size:9px;color:#fff2d8;margin-top:5px;letter-spacing:.5px}
.blog-text{font-size:10px;color:var(--white);line-height:13px;font-weight:700;margin-bottom:8px}
.social{display:flex;gap:18px;margin-top:12px}
.social-item{width:26px;text-align:center}
.social-item i{display:block;width:26px;height:26px;border-radius:3px}
.social-item span{display:block;font-size:7px;color:var(--white);margin-top:2px;font-style:normal}
.plus{display:flex;align-items:center;gap:3px;margin-top:4px}
.plus b{width:24px;height:15px;background:#eef3fb;border:1px solid #99a;border-radius:2px;font-size:9px;color:#336;text-align:center;line-height:13px}
.plus span{background:var(--white);border:1px solid #ccc;font-size:9px;padding:0 4px;line-height:14px}
.like{display:flex;align-items:center;gap:5px;margin-top:5px;font-size:9px;color:var(--white)}
.like b{background:#eceef5;border:1px solid #cad4e7;border-radius:2px;font-size:10px;color:#3b5998;padding:1px 5px;display:flex;align-items:center;gap:3px}
.like i{display:inline-block;width:9px;height:9px;background:#3b5998}
.bottom{left:0;top:1150px;width:1000px;height:50px;background:#222}
.bottom-brand{left:95px;top:1155px;width:72px;text-align:center}
.bottom-brand i{display:block;width:18px;height:18px;margin:0 auto 4px;background:var(--gold)}
.bottom-brand b{display:block;font-weight:400;font-size:9px;color:var(--gold-text);line-height:10px}
.legal{left:175px;top:1166px;font-size:10px;color:#888;line-height:14px}
.legal strong{color:#ddd;font-weight:400}
</style>
</head>
<body>
<div class="abs top-band"></div>

<div class="abs brand">
  <span class="brand-mark"></span>
  <div class="brand-name">LAKE VORISSA</div>
  <div class="brand-sub">REAL ESTATE</div>
</div>

<div class="abs login">
  <div class="login-title">Client Login</div>
  <div class="login-row">
    <div class="login-input">Username</div>
    <div class="login-input">Password</div>
    <div class="login-btn">LOGIN</div>
  </div>
  <div class="login-help">Forgot your password? / Register</div>
</div>

<nav class="abs nav">
  <a>Home</a><a>Company</a><a>Associates</a><a>Search Properties</a><a>Marketing and Design</a><a>Contact</a>
</nav>

<div class="abs hero"></div>
<div class="abs hero-photo" role="img" aria-label="Photo of a two-storey suburban family house with porch, lawn and trees"></div>
<svg class="abs hero-arrow" style="left:75px" viewBox="0 0 52 52"><path d="M32 16 L22 26 L32 36" fill="none" stroke="#fff" stroke-width="4"/></svg>
<svg class="abs hero-arrow" style="left:872px" viewBox="0 0 52 52"><path d="M20 16 L30 26 L20 36" fill="none" stroke="#fff" stroke-width="4"/></svg>

<div class="abs welcome-band"></div>
<div class="abs welcome">
  <h1>Welcome to</h1>
  <h2>Lake Vorissa Real Estate</h2>
  <p>Lorem ipsum dolor sit amet, consectetur adipisicing elit, sed do eiusmod tempor incididunt ut labore et dolore magna aliqua. Ut enim ad minim veniam, quis nostrud exercitation ullamco laboris nisi ut aliquip ex ea commodo consequat. Duis aute irure dolor in reprehenderit in voluptate velit esse cillum dolore eu fugiat nulla pariatur. Excepteur sint occaecat cupidatat non proident, sunt in culpa qui officia deserunt mollit anim id est laborum.</p>
</div>

<div class="abs search-tab">PROPERTYES SEARCH</div>
<div class="abs search">
  <div class="quick">
    <div class="quick-label">QUICK<br>SEARCH</div>
    <div class="quick-field-label">MLS # or Street Name</div>
    <div class="field" style="left:84px;top:23px;width:245px;height:22px"></div>
    <div class="go">GO</div>
  </div>
  <div class="field-label" style="left:19px;top:56px">City</div>
  <div class="field" style="left:19px;top:75px;width:165px;height:24px"></div>
  <div class="field-label" style="left:200px;top:56px">Location</div>
  <div class="field select" style="left:200px;top:75px;width:164px;height:24px">Any</div>
  <div class="field-label" style="left:19px;top:109px">Price</div>
  <div class="field select" style="left:19px;top:129px;width:78px;height:24px">Any</div>
  <div class="field-label" style="left:102px;top:133px;font-size:10px">to</div>
  <div class="field select" style="left:114px;top:129px;width:78px;height:24px">Any</div>
  <div class="field-label" style="left:200px;top:109px">Beds</div>
  <div class="field select" style="left:200px;top:129px;width:78px;height:24px">Any</div>
  <div class="field-label" style="left:286px;top:109px">Baths</div>
  <div class="field select" style="left:286px;top:129px;width:78px;height:24px">Any</div>
  <div class="btn" style="left:20px;top:170px;width:120px">PROPERTY SEARCH</div>
  <div class="btn" style="left:153px;top:170px;width:115px">SEARCH BY MLS #</div>
  <div class="adv">Advanced Search</div>
</div>

<div class="abs footer-band"></div>
<div class="abs content"></div>

<section class="abs news">
  <div class="news-head"><h3>News</h3><span>VIEW ALL ▸</span></div>
  <div class="news-item"><div class="date"><b>31</b>Oct<br>2011</div><div><h4>Lorem ipsum dolor sit</h4><p>Lorem ipsum dolor sit amet, consectetur adipisicing elit, sed do eiusmod tempor incididunt</p></div></div>
  <div class="news-item"><div class="date"><b>31</b>Oct<br>2011</div><div><h4>Lorem ipsum dolor sit</h4><p>Lorem ipsum dolor sit amet, consectetur adipisicing elit, sed do eiusmod tempor incididunt</p></div></div>
  <div class="news-item"><div class="date"><b>31</b>Oct<br>2011</div><div><h4>Lorem ipsum dolor sit</h4><p>Lorem ipsum dolor sit amet, consectetur adipisicing elit, sed do eiusmod tempor incididunt</p></div></div>
</section>

<h3 class="abs col-title" style="left:354px;top:710px">Feature Property</h3>
<div class="abs feature-back"></div>
<div class="abs feature-photo" role="img" aria-label="Photo of a white colonial house with a columned front porch"></div>
<svg class="abs slide-btn" style="left:342px;top:826px" viewBox="0 0 24 28"><path d="M15 8 L9 14 L15 20" fill="none" stroke="#333" stroke-width="2"/></svg>
<svg class="abs slide-btn" style="left:556px;top:818px" viewBox="0 0 24 28"><path d="M9 8 L15 14 L9 20" fill="none" stroke="#333" stroke-width="2"/></svg>
<p class="abs small-text" style="left:363px;top:931px;width:190px;line-height:16px">Lorem ipsum dolor sit amet, consectetur adipisicing elit, sed do eiusmod tempor incididunt ut labore et dolore.</p>

<div class="abs divider"></div>

<h3 class="abs col-title" style="left:620px;top:710px">Neighbourhood area</h3>
<div class="abs map" role="img" aria-label="Map of the United States showing the neighbourhood areas"></div>
<p class="abs small-text" style="left:770px;top:749px;width:110px">Lorem ipsum dolor sit amet, consectetur adipisicing elit, sed do eiusmod tempor incididunt ut labore et dolore magna aliqua.</p>

<section class="abs testimonials">
  <h3>Testimonials</h3>
  <p>Lorem ipsum dolor sit amet, consectetur adipisicing elit, sed do eiusmod tempor incididunt ut labore et dolore magna</p>
  <p style="text-align:right;font-style:normal;font-weight:700;color:#222;font-size:11px;margin-top:5px;line-height:13px">Lorem ipsum</p>
  <p style="text-align:right;line-height:13px;padding-right:14px">dolor sit</p>
</section>

<div class="abs" style="left:101px;top:1030px">
  <div class="f-title">Quick Links</div>
  <div class="f-links"><a>Home</a><a>BLog</a><a>About Us</a><a>Testimonials</a><a>Search Properties</a><a>Contact</a><a>News</a></div>
</div>

<div class="abs" style="left:303px;top:1033px;width:190px">
  <div class="mail-title">JOIN OUR MAILING LIST</div>
  <div class="mail-text">Sign up for our e-mail list to<br>receive updates</div>
  <div class="mail-field">Your e-mail address<div class="mail-join">JOIN</div></div>
</div>

<div class="abs" style="left:521px;top:1030px;width:190px">
  <div class="f-title">Blog</div>
  <div class="blog-date">09 April 2012</div>
  <div class="blog-text">Lorem ipsum dolor sit amet, consectetur adipisicing elit, sed do</div>
  <div class="blog-date">06 April 2012</div>
  <div class="blog-text">Lorem ipsum dolor sit amet, consectetur adipisicing elit, sed do</div>
</div>

<div class="abs" style="left:735px;top:1030px;width:170px">
  <div class="f-title">Connect With Us</div>
  <div class="social">
    <div class="social-item"><i style="background:#3b5998"></i><span>Friendloop</span></div>
    <div class="social-item"><i style="background:#5ab8d8"></i><span>Chirpline</span></div>
    <div class="social-item"><i style="background:#1a6fa0"></i><span>Netlinker</span></div>
    <div class="social-item"><i style="background:#ef8a1c"></i><span>Feed</span></div>
  </div>
  <div class="plus"><b>+1</b><span>17</span></div>
  <div class="like"><b><i></i>Like</b>2,942 people like this.</div>
</div>

<div class="abs bottom"></div>
<div class="abs bottom-brand"><i></i><b>LAKE VORISSA</b><b>REAL ESTATE</b></div>
<div class="abs legal">Terms of Use | Privacy Policy<br><strong>© 2011 Lake Vorissa Real Estate .All Rights Reserved</strong></div>
</body>
</html>
```